Velmarotix - world unique technology for better life - please let them know who am i at first sight

We need a new business card for company which is a provider of unique crystal based technology suitable for all living being. For more information and final design you can use our brochure (our colours are black and blue from brochure).
We use Verdana font

Industry/Entity Type

Business

Contact Information for Business Card

regular dimension

Font styles to use
Other font styles liked:
• Verdana

Requirements
Must have
• Logo
• name
• function/position
• phone
• mobile
• e-mail
• adress
Nice to have
• inovative design (technology directed)

```html
<!DOCTYPE html>
<html lang="en">
<head>
<meta charset="utf-8">
<title>Velmarotix Business Card</title>
<link rel="stylesheet" href="https://fonts.googleapis.com/css2?family=Noto+Sans:wght@300;400;700&display=swap">
<style>
  :root {
    --page: #ece6d2;
    --card-black: #0b0b0c;
    --card-white: #fbfbfb;
    --card-grey: #d9dadb;
    --brand-blue: #1ba6e0;
    --brand-blue-deep: #0d7fb8;
    --ink: #1c1c1c;
    --paper-text: #f2f2f2;
    --rule: #3a3f44;
  }
  * { box-sizing: border-box; margin: 0; padding: 0; }
  html, body { width: 1200px; height: 978px; overflow: hidden; }
  body {
    background: var(--page);
    font-family: "Noto Sans", Verdana, sans-serif;
    display: flex;
    flex-direction: column;
    align-items: center;
    justify-content: center;
    gap: 70px;
  }
  .card {
    width: 620px;
    height: 354px;
    border-radius: 26px;
    position: relative;
    overflow: hidden;
  }

  /* Front */
  .card-front {
    background: radial-gradient(ellipse at 50% 40%, var(--card-white) 0%, var(--card-white) 35%, var(--card-grey) 100%);
    display: flex;
    flex-direction: column;
    align-items: center;
    justify-content: center;
  }
  .front-mark {
    display: flex;
    align-items: center;
    gap: 18px;
    margin-top: -10px;
  }
  .front-mark .dot {
    width: 34px; height: 34px;
    border-radius: 50%;
    background: var(--brand-blue);
  }
  .front-mark .wordmark {
    font-weight: 300;
    font-size: 46px;
    letter-spacing: 6px;
    color: var(--brand-blue);
  }
  .front-url {
    margin-top: 64px;
    font-size: 17px;
    font-weight: 700;
    letter-spacing: 2.5px;
    color: var(--ink);
  }

  /* Back */
  .card-back {
    background: var(--card-black);
    color: var(--paper-text);
    padding: 34px 44px 0 70px;
  }
  .back-glow {
    position: absolute;
    left: 180px; top: 70px;
    width: 250px; height: 250px;
    border-radius: 50%;
    background: radial-gradient(circle, rgba(27,166,224,0.16) 0%, rgba(27,166,224,0.05) 60%, rgba(27,166,224,0) 75%);
  }
  .back-wordmark {
    position: relative;
    display: block;
    text-align: center;
    font-weight: 300;
    font-size: 42px;
    letter-spacing: 9px;
    color: var(--brand-blue);
    margin-left: 40px;
  }
  .back-rule {
    position: relative;
    height: 1px;
    background: var(--rule);
    margin: 18px 0 22px -70px;
  }
  .person { position: relative; font-size: 17px; }
  .person .name { color: var(--brand-blue); font-weight: 700; }
  .person .role { color: var(--paper-text); font-weight: 400; }
  .contacts {
    position: relative;
    margin-top: 16px;
    display: grid;
    grid-template-columns: auto auto;
    column-gap: 34px;
    row-gap: 12px;
    justify-content: start;
    font-size: 13.5px;
  }
  .contact { display: flex; align-items: center; gap: 8px; }
  .contact svg { width: 14px; height: 14px; fill: none; stroke: var(--paper-text); stroke-width: 1.6; }
  .address { position: relative; margin-top: 14px; font-size: 13.5px; }
</style>
</head>
<body>
  <section class="card card-front">
    <div class="front-mark">
      <span class="dot"></span>
      <span class="wordmark">Velmarotix</span>
    </div>
    <p class="front-url">www.velmarotix.cu</p>
  </section>

  <section class="card card-back">
    <div class="back-glow" role="img" aria-label="Faint blue glow decoration"></div>
    <span class="back-wordmark">VELMAROTIX</span>
    <div class="back-rule"></div>
    <p class="person"><span class="name">Mira Kostanjevec,</span> <span class="role">Founder and CEO</span></p>
    <div class="contacts">
      <span class="contact">
        <svg viewBox="0 0 16 16"><path d="M4 2l2.5 3-1.5 1.5c.8 1.8 2.2 3.2 4 4l1.5-1.5 3 2.5-1.5 2.5C7 13.5 2.5 9 1.5 3.5z"/></svg>
        012-555-0148
      </span>
      <span class="contact">
        <svg viewBox="0 0 16 16"><rect x="4.5" y="1.5" width="7" height="13" rx="1.2"/><line x1="7" y1="12" x2="9" y2="12"/></svg>
        012-555-0149
      </span>
      <span class="contact">
        <svg viewBox="0 0 16 16"><rect x="1.5" y="3.5" width="13" height="9" rx="1"/><path d="M1.5 4l6.5 5 6.5-5"/></svg>
        info@velmarotix.cu
      </span>
      <span class="contact">
        <svg viewBox="0 0 16 16"><circle cx="8" cy="8" r="6.5"/><path d="M1.5 8h13M8 1.5c2 2 2 11 0 13M8 1.5c-2 2-2 11 0 13"/></svg>
        www.velmarotix.cu
      </span>
    </div>
    <p class="address">Street Number, Street Name, Zipcode 01234</p>
  </section>
</body>
</html>
```